Investment company needing business card

We are wanting a business card which looks sharp and easy on the eye. We are thinking of having a business card with the logo embossed on it, to really make it stand out. We will only have a small amount of information of the business card, person's name, position, email address and phone number

Contact Information for Business Card

Danielle Frost
Executive Assistant
+64 21 473 5162
danielf@harwickpartners.co.nz

Requirements
Must have
• Embossed logo
Should not have
• Not to be busy

```html
<!DOCTYPE html>
<html lang="en">
<head>
<meta charset="utf-8">
<title>Harwick Partners – Business Card</title>
<link rel="stylesheet" href="https://fonts.googleapis.com/css2?family=Open+Sans:wght@400;700&display=swap">
<style>
  :root {
    --brand-green: #2fb874;
    --brand-green-deep: #25a063;
    --charcoal: #666668;
    --ink: #555558;
    --paper: #ffffff;
    --backdrop: #e9eaec;
    --rule: #8a8a8c;
  }
  * { box-sizing: border-box; margin: 0; padding: 0; }
  html, body {
    width: 1200px; height: 862px; overflow: hidden;
    background: var(--backdrop);
    font-family: "Open Sans", Arial, sans-serif;
  }
  .canvas { position: relative; width: 1200px; height: 862px; }

  .card {
    position: absolute;
    width: 560px; height: 320px;
    border-radius: 90px 6px 6px 90px;
    box-shadow: 0 10px 28px rgba(0,0,0,0.18);
  }

  /* Front: embossed wordmark on green */
  .card-front {
    left: 90px; top: 80px;
    background: var(--brand-green);
    display: flex; align-items: center; justify-content: center;
  }
  .front-mark {
    display: flex; align-items: center; gap: 14px;
    color: var(--brand-green-deep);
    font-weight: 700; font-size: 34px; letter-spacing: 3px;
    text-transform: uppercase;
  }
  .front-mark .mark-square {
    width: 40px; height: 40px; background: var(--brand-green-deep);
  }

  /* Back: contact details */
  .card-back {
    left: 550px; top: 440px;
    background: var(--paper);
    display: flex; align-items: center;
    padding: 0 30px 0 40px;
  }
  .back-mark {
    width: 220px;
    display: flex; align-items: center; gap: 12px;
    color: var(--charcoal);
    font-weight: 700; font-size: 24px; line-height: 1.15;
  }
  .back-mark .mark-square {
    flex: none; width: 34px; height: 34px; background: var(--brand-green);
  }
  .divider {
    width: 1px; height: 170px; background: var(--rule);
    margin: 0 24px 0 14px;
  }
  .details { color: var(--ink); font-size: 13px; line-height: 1.55; }
  .details .name {
    color: var(--brand-green); font-weight: 700; font-size: 21px; line-height: 1.2;
  }
  .details .role { margin-bottom: 6px; }
  .details .address { margin-bottom: 6px; }
  .contact-row { display: flex; align-items: center; gap: 8px; }
  .contact-row svg { width: 12px; height: 12px; flex: none; }
</style>
</head>
<body>
<div class="canvas">
  <section class="card card-front">
    <div class="front-mark"><span class="mark-square"></span>Harwick Partners</div>
  </section>

  <section class="card card-back">
    <div class="back-mark"><span class="mark-square"></span>Harwick Partners</div>
    <div class="divider"></div>
    <div class="details">
      <div class="name">Danielle Frost</div>
      <div class="role">Executive Assistant</div>
      <div class="address">1428 Larkspur Avenue<br>Oakland, CA 94610</div>
      <div class="contact-row">
        <svg viewBox="0 0 24 24"><path fill="var(--brand-green)" d="M6.6 10.8a15 15 0 0 0 6.6 6.6l2.2-2.2a1 1 0 0 1 1-.25 11.4 11.4 0 0 0 3.6.57 1 1 0 0 1 1 1V20a1 1 0 0 1-1 1A17 17 0 0 1 3 4a1 1 0 0 1 1-1h3.5a1 1 0 0 1 1 1c0 1.25.2 2.45.57 3.57a1 1 0 0 1-.25 1z"/></svg>
        <span>+64 21 473 5162</span>
      </div>
      <div class="contact-row">
        <svg viewBox="0 0 24 24"><rect x="2.5" y="5" width="19" height="14" fill="none" stroke="var(--brand-green)" stroke-width="2"/><path d="M2.5 5l9.5 8 9.5-8" fill="none" stroke="var(--brand-green)" stroke-width="2"/></svg>
        <span>danielf@harwickpartners.co.nz</span>
      </div>
      <div class="contact-row">
        <svg viewBox="0 0 24 24"><circle cx="12" cy="12" r="9.5" fill="none" stroke="var(--brand-green)" stroke-width="2"/><path d="M2.5 12h19M12 2.5c3 3 3 16 0 19M12 2.5c-3 3-3 16 0 19" fill="none" stroke="var(--brand-green)" stroke-width="1.6"/></svg>
        <span>www.harwickpartners.co.nz</span>
      </div>
    </div>
  </section>
</div>
</body>
</html>
```